Vortel surface design based website for technology jobs website

We need a website design for a technology job listing website, mainly aiming at 20/30/40 year old nerds. Jobs listed from multiple sources will be concatenated and organised. This website will be built with Vortel surface design (https://surfacekit.example/guidelines/) so please use their components. The design should be simple and clear, so a user can directly look for offerings that are interesting for him.

Three different pages will be needed:

1. Main jobs list page

Contains a large table (https://surfacekit.example/guidelines/components/data-tables.html#data-tables-structure), on top or next to this data-table users should be able to apply filters (select countries, select salary ranges) and somewhere an overview of the selected filters should be shown.

- A subscribe bar should be shown somewhere to allow a user to register for weekly/monthly mailings for new job offers with his preferred search filters.

2. Selected item page

If an item is clicked, a user should be able to view a job posting and it's details.

3. An advertiser should be able post his job offer.
Similar fields as https://post.ledgerworkboard.example/.
(https://surfacekit.example/guidelines/components/text-fields.html#text-fields-layout)

Target Market(s)

20/30/40 year old nerds.

Industry/Entity Type

Computer

Logo Text

TechHirePlaza.example

Number of Pages Required

3 page

Colors

Designer to choose colors to be used in the design.

Requirements
Must have
• 1. Main jobs list page
• Contains a large table (https://surfacekit.example/guidelines/components/data-tables.html#data-tables-structure), on top or next to this data-table users should be able to apply filters (select countries, select salary ranges) and somewhere an overview of the selected filters should be shown.
• - A subscribe bar should be shown somewhere to allow a user to register for weekly/monthly mailings for new job offers with his preferred search filters.
• 2. Selected item page
• If an item is clicked, a user should be able to view a job posting and it's details.
• 3. An advertiser should be able post his job offer,
• (https://surfacekit.example/guidelines/components/text-fields.html#text-fields-layout)
• Please use open fonts!

```html
<!DOCTYPE html>
<html lang="en">
<head>
<meta charset="utf-8">
<title>Job Listings</title>
<link href="https://fonts.googleapis.com/css2?family=Roboto:wght@300;400;500;700&display=swap" rel="stylesheet">
<style>
:root{
  --brand-deep:#0158a0;
  --brand-bright:#05a8f2;
  --brand-button:#0a4d94;
  --link:#0a9be0;
  --text:#333a40;
  --muted:#6b7177;
  --page:#efefef;
  --row-line:#e8ecef;
  --row-selected:#f2f2f2;
  --detail-bg:#eaf3fb;
  --subscribe-title:#3a8fc7;
  --send:#6fb4e8;
  --fab:#e0392b;
  --footer:#2d3035;
  --white:#ffffff;
}
*{box-sizing:border-box;margin:0;padding:0}
html,body{width:1136px;height:1200px;overflow:hidden}
body{position:relative;background:var(--page);font-family:"Roboto",sans-serif;color:var(--text)}
.hero{position:absolute;left:0;top:0;width:1136px;height:374px;background:var(--brand-deep)}
.menu-icon{position:absolute;left:81px;top:21px}
.logo{position:absolute;left:0;width:1136px;top:6px;text-align:center;color:var(--white);font-weight:700;font-size:30px}
.search-panel{position:absolute;left:81px;top:98px;width:973px;height:92px;background:var(--brand-bright)}
.field{position:absolute;top:27px;height:39px;background:var(--white);border-radius:2px;display:flex;align-items:center;justify-content:space-between;padding:0 7px;font-size:11.5px;color:#8a8f94}
.field svg{flex:none}
.search-btn{position:absolute;left:850px;top:27px;width:96px;height:39px;background:var(--brand-button);border-radius:2px;display:flex;align-items:center;justify-content:center}
.jobs-card{position:absolute;left:81px;top:252px;width:973px;height:866px;background:var(--white);box-shadow:0 1px 3px rgba(0,0,0,.2)}
.row{position:relative;height:47.4px;border-bottom:1px solid var(--row-line);font-size:12px;color:var(--muted)}
.row.head{height:45px;color:var(--text)}
.row.selected{background:var(--row-selected);border-bottom:1px solid #9aa0a5}
.row span{position:absolute;top:50%;transform:translateY(-50%);white-space:nowrap}
.check{position:absolute;left:13px;top:50%;transform:translateY(-50%);width:12px;height:12px;border:1px solid #8d9398;border-radius:1px;background:var(--white)}
.c-type{left:32px;color:var(--link)}
.c-country{left:227px}.c-exp{left:403px}.c-sal{left:557px}.c-skill{left:687px}.c-emp{left:829px}
.head .c-type{color:var(--link)}
.detail{height:207px;background:var(--detail-bg);position:relative;font-size:12px;color:var(--text)}
.detail-title{position:absolute;left:14px;top:13px;color:#0d4a78}
.detail-meta{position:absolute;left:12px;top:35px;display:flex;align-items:center;gap:6px;font-size:11.5px}
.detail-label{position:absolute;left:12px;font-size:11.5px}
.detail-value{position:absolute;left:134px;width:800px;line-height:16.6px;font-size:11.5px}
.detail-divider{position:absolute;left:2px;right:2px;top:164px;border-top:1px solid #b9c2c9}
.apply{position:absolute;left:14px;top:174px;width:68px;height:19px;background:var(--brand-bright);color:var(--white);font-size:11.5px;display:flex;align-items:center;justify-content:center;border-radius:2px}
.detail-stats{position:absolute;right:13px;top:178px;font-size:10px;display:flex;gap:15px}
.subscribe{position:absolute;left:701px;top:853px;width:421px;height:199px;background:var(--white);box-shadow:0 1px 4px rgba(0,0,0,.35);text-align:center}
.subscribe h2{margin-top:27px;font-weight:300;font-size:21.5px;color:var(--subscribe-title)}
.subscribe p{margin:4px auto 0;width:300px;font-weight:300;font-size:11.5px;line-height:20px;color:var(--muted)}
.sub-input{position:absolute;top:112px;width:167px;height:14px;border-bottom:1px solid #d8dbde;text-align:left;font-size:11.5px;color:var(--muted);padding-bottom:16px}
.send{position:absolute;left:171px;top:138px;width:77px;height:27px;background:var(--send);color:var(--white);font-size:12px;border-radius:2px;display:flex;align-items:center;justify-content:center}
.fab{position:absolute;left:1068px;top:1061px;width:56px;height:56px;border-radius:50%;background:var(--fab);display:flex;align-items:center;justify-content:center}
.footer{position:absolute;left:0;top:1162px;width:1136px;height:38px;background:var(--footer);color:var(--white);font-size:11.5px;display:flex;align-items:center;justify-content:center}
</style>
</head>
<body>
<header class="hero">
  <svg class="menu-icon" width="23" height="16" viewBox="0 0 23 16"><rect y="0" width="23" height="2.2" fill="#fff"/><rect y="6.9" width="23" height="2.2" fill="#fff"/><rect y="13.8" width="23" height="2.2" fill="#fff"/></svg>
  <div class="logo">Logo Name</div>
  <div class="search-panel">
    <div class="field" style="left:29px;width:276px">Keyword e.g. ( jobTitle, Description,Tags)<svg width="8" height="5"><path d="M0 0l4 4 4-4" stroke="#888" fill="none"/></svg></div>
    <div class="field" style="left:313px;width:203px">Select Location<svg width="8" height="5"><path d="M0 0l4 4 4-4" stroke="#888" fill="none"/></svg></div>
    <div class="field" style="left:524px;width:202px">Salary<svg width="8" height="5"><path d="M0 0l4 4 4-4" stroke="#888" fill="none"/></svg></div>
    <div class="field" style="left:735px;width:107px">Designation<svg width="8" height="5"><path d="M0 0l4 4 4-4" stroke="#888" fill="none"/></svg></div>
    <div class="search-btn"><svg width="19" height="19" viewBox="0 0 19 19"><circle cx="8" cy="8" r="6" stroke="#fff" stroke-width="2.6" fill="none"/><path d="M12.5 12.5l5 5" stroke="#fff" stroke-width="3" stroke-linecap="round"/></svg></div>
  </div>
</header>

<main class="jobs-card">
  <div class="row head"><i class="check"></i><span class="c-type">Job Type</span><span class="c-country">Country Name</span><span class="c-exp">Experience</span><span class="c-sal">Salary</span><span class="c-skill">Keyskills</span><span class="c-emp">Employment Type</span></div>
  <div class="row"><i class="check"></i><span class="c-type">Software Engineer</span><span class="c-country">Country</span><span class="c-exp">0 -1</span><span class="c-sal">$ 20000</span><span class="c-skill">HTML Javascript ⌄</span><span class="c-emp">Full Time</span></div>
  <div class="row selected"><i class="check" style="border-color:#b5babe"><svg width="10" height="10" style="position:absolute;left:0;top:0"><path d="M2 5l2.3 2.3L8.5 2.5" stroke="#9aa0a5" stroke-width="1.3" fill="none"/></svg></i><span class="c-type">Software Engineer</span><span class="c-country">Country</span><span class="c-exp">0 -1</span><span class="c-sal">$ 20000</span><span class="c-skill">HTML Javascript ⌄</span><span class="c-emp">Full Time</span></div>
  <section class="detail">
    <div class="detail-title">Software Engineer</div>
    <div class="detail-meta">
      <svg width="11" height="11" viewBox="0 0 11 11"><circle cx="5.5" cy="5.5" r="4.3" stroke="#222" stroke-width="1.5" fill="none"/><path d="M5.5 3v2.7h2" stroke="#222" stroke-width="1.2" fill="none"/></svg>
      <span>0 - 5 years</span>
      <svg width="10" height="13" viewBox="0 0 10 13" style="margin-left:8px"><path d="M5 0C2.2 0 0 2.2 0 4.9 0 8.5 5 13 5 13s5-4.5 5-8.1C10 2.2 7.8 0 5 0z" fill="#222"/><circle cx="5" cy="4.8" r="1.8" fill="#eaf3fb"/></svg>
      <span>Country</span>
    </div>
    <div class="detail-label" style="top:62px">Keyskills :</div>
    <div class="detail-value" style="top:62px">Java.css, software.....</div>
    <div class="detail-label" style="top:96px">Job Description :</div>
    <div class="detail-value" style="top:95px">Lorem Ipsum is simply dummy text of the printing and typesetting industry. Lorem Ipsum has been the industry's standard dummy text ever since the 1500s,&nbsp;&nbsp;&nbsp;&nbsp; orem Ipsum is simply dummy text of the printing and typesetting industry. Lorem Ipsum has been the industry's standard dummy text ever since the 1500s, when an unknown printer took a galley of type and scrambled it to</div>
    <div class="detail-divider"></div>
    <div class="apply">Apply</div>
    <div class="detail-stats"><span>Job Views: 19</span><span>Posted Few Hours Ago</span></div>
  </section>
  <div class="row"><i class="check"></i><span class="c-type">Software Engineer</span><span class="c-country">Country</span><span class="c-exp">0 -1</span><span class="c-sal">$ 20000</span><span class="c-skill">HTML Javascript ⌄</span><span class="c-emp">Full Time</span></div>
  <div class="row"><i class="check"></i><span class="c-type">Software Engineer</span><span class="c-country">Country</span><span class="c-exp">0 -1</span><span class="c-sal">$ 20000</span><span class="c-skill">HTML Javascript ⌄</span><span class="c-emp">Full Time</span></div>
  <div class="row"><i class="check"></i><span class="c-type">Software Engineer</span><span class="c-country">Country</span><span class="c-exp">0 -1</span><span class="c-sal">$ 20000</span><span class="c-skill">HTML Javascript ⌄</span><span class="c-emp">Full Time</span></div>
  <div class="row"><i class="check"></i><span class="c-type">Software Engineer</span><span class="c-country">Country</span><span class="c-exp">0 -1</span><span class="c-sal">$ 20000</span><span class="c-skill">HTML Javascript ⌄</span><span class="c-emp">Full Time</span></div>
  <div class="row"><i class="check"></i><span class="c-type">Software Engineer</span><span class="c-country">Country</span><span class="c-exp">0 -1</span><span class="c-sal">$ 20000</span><span class="c-skill">HTML Javascript ⌄</span><span class="c-emp">Full Time</span></div>
  <div class="row"><i class="check"></i><span class="c-type">Software Engineer</span><span class="c-country">Country</span><span class="c-exp">0 -1</span><span class="c-sal">$ 20000</span><span class="c-skill">HTML Javascript ⌄</span><span class="c-emp">Full Time</span></div>
  <div class="row"><i class="check"></i><span class="c-type">Software Engineer</span><span class="c-country">Country</span><span class="c-exp">0 -1</span><span class="c-sal">$ 20000</span><span class="c-skill">HTML Javascript ⌄</span><span class="c-emp">Full Time</span></div>
  <div class="row"><i class="check"></i><span class="c-type">Software Engineer</span><span class="c-country">Country</span><span class="c-exp">0 -1</span><span class="c-sal">$ 20000</span><span class="c-skill">HTML Javascript ⌄</span><span class="c-emp">Full Time</span></div>
  <div class="row"><i class="check"></i><span class="c-type">Software Engineer</span><span class="c-country">Country</span><span class="c-exp">0 -1</span><span class="c-sal">$ 20000</span><span class="c-skill">HTML Javascript ⌄</span><span class="c-emp">Full Time</span></div>
  <div class="row"><i class="check"></i><span class="c-type">Software Engineer</span><span class="c-country">Country</span><span class="c-exp">0 -1</span><span class="c-sal">$ 20000</span><span class="c-skill">HTML Javascript ⌄</span><span class="c-emp">Full Time</span></div>
</main>

<aside class="subscribe">
  <h2>Subscribe to our newsletter</h2>
  <p>Lorem Ipsum is simply dummy text of the printing and typesetting industry.</p>
  <div class="sub-input" style="left:34px">Name</div>
  <div class="sub-input" style="left:218px">Email Id</div>
  <div class="send">Send</div>
</aside>

<div class="fab"><svg width="20" height="20" viewBox="0 0 20 20"><path d="M10 1v18M1 10h18" stroke="#fff" stroke-width="2"/></svg></div>

<footer class="footer">Copyright © website address I All Rights Reaserved</footer>
</body>
</html>
```